Creation of a construction/bricklaying business website

Following the template format of "Halloway 7", the following content would need to be included:
1. Landing page with 3 tiles that go to their own pages.
- Landing page to include background photo and description of services offered.
2. 3 tiles to include:
a) "Contact Us For A Free Quote or Friendly Discussion" Form (middle tile)
b) Case Studies and Testimonials
c) Certifications and Professional Membership
- Design logo to be used from previous SketchNestle project. Example of logo attached below, please access full JPG files from our account.

Target Market(s)

Prospective clients seeking construction work (bricklaying speciality)

Industry/Entity Type

Residential Construction

Coding

Coded - Design and coding required

Number of Pages Required

4 page

Font styles to use
Sans Serif

Colors

Designer to choose colors to be used in the design.

Requirements
Must have
• Following the template format of "Halloway 7", the following content would need to be included:
• 1. Landing parent page with 3 tiles that go to the 3 child pages.
• - Landing page to include background photo and description of services offered.
• 2. 3 tiles to include:
• a) "Contact Us For A Free Quote or Friendly Discussion" Form (middle tile)
• b) Case Studies and Testimonials (first tile / left side)
• c) Certifications and Professional Memberships (third tile / right side) (This should include logos of the relevant organisations being displayed. Specifically GQT and the Pillar Seal GQT).
• - Design logo to be used from previous SketchNestle project. Example of logo attached below, please access full JPG files from our account.
Nice to have
• Sleek and modern feel.
• Approachable in terms of how people can contact the company for a quote.
• Traditional pictures to give credibility and comfort around choosing this company.
Should not have
• Cheesy pictures
• Over-complicated
• Simple to use
• Easy URL domain name

```html
<!DOCTYPE html>
<html lang="en">
<head>
<meta charset="utf-8">
<title>R.T.Marlow Construction Ltd – Website Layout</title>
<link href="https://fonts.googleapis.com/css2?family=Jost:wght@400;500;600&family=Oswald:wght@500;600&display=swap" rel="stylesheet">
<style>
:root{
  --stage:#ececec;
  --page:#f1f1f1;
  --white:#ffffff;
  --ink:#222222;
  --muted:#777777;
  --line:#dddddd;
  --blue:#1a57b5;
  --blue-dark:#124596;
  --dark:#262626;
  --darker:#1b1b1b;
  --bar:#2d2f33;
  --red:#b3222d;
}
*{box-sizing:border-box;margin:0;padding:0}
html,body{width:1200px;height:3766px;overflow:hidden}
body{background:var(--stage);font-family:"Jost",sans-serif;color:var(--ink);position:relative}

.view{position:absolute;background:var(--page);box-shadow:0 2px 10px rgba(0,0,0,.12);overflow:hidden}
.view--desktop{left:50px;top:43px;width:776px}
.view--mobile{left:889px;top:120px;width:262px}

/* hero */
.hero{position:relative;height:316px;color:var(--white);text-align:center}
.view--mobile .hero{height:432px}
.hero__photo{position:absolute;inset:0;background:linear-gradient(180deg,#1d2a3d 0%,#33455c 45%,#3e4a58 70%,#5a4a3a 100%)}
.hero__shade{position:absolute;inset:0;background:rgba(15,22,35,.35)}
.hero__inner{position:relative;padding-top:46px}
.view--mobile .hero__inner{padding-top:60px}
.brand{display:inline-flex;align-items:center;gap:6px;font-weight:600;font-size:15px;letter-spacing:.5px}
.brand__mark{width:10px;height:10px;background:var(--white)}
.brand small{display:block;font-size:7px;letter-spacing:1.5px;font-weight:600}
.hero__title{font-size:42px;font-weight:500;color:rgba(255,255,255,.4);margin-top:26px;letter-spacing:1px}
.view--mobile .hero__title{font-size:34px;margin-top:36px}
.services{display:flex;justify-content:center;flex-wrap:wrap;gap:4px 10px;margin-top:26px;font-family:"Oswald",sans-serif;font-size:9px;font-weight:600;list-style:none}
.view--mobile .services{padding:0 28px;gap:14px 12px;margin-top:22px}
.services li::before{content:"• "}
.services li:first-child::before{content:""}
.services .is-active{color:#7fa8ff;border-bottom:1px solid #7fa8ff}

.menubar{height:30px;background:var(--bar);display:flex;align-items:center;padding:0 100px;gap:34px;font-size:6.5px;letter-spacing:.6px;color:#aaaaaa;text-transform:uppercase}
.menubar__search{margin-left:auto}
.view--mobile .menubar{padding:0 12px}

/* sections */
.section{padding:42px 0 40px;text-align:center}
.section--white{background:var(--white)}
.section--grey{background:var(--page)}
.section__title{display:inline-block;font-size:17px;font-weight:600;border-bottom:2px solid var(--blue);padding-bottom:1px;margin-bottom:20px}
.view--mobile .section__title{font-size:15px}

.cards{display:grid;grid-template-columns:repeat(3,151px);gap:44px;justify-content:center;text-align:left}
.view--mobile .cards{grid-template-columns:176px;gap:34px}
.card{background:var(--white);box-shadow:0 1px 4px rgba(0,0,0,.12)}
.card__title{font-family:"Oswald",sans-serif;font-size:9px;font-weight:500;padding:14px 9px 12px}
.card__photo{height:66px}
.view--mobile .card__photo{height:70px}
.card__photo--a{background:linear-gradient(120deg,#d8cfc7,#b9453c 55%,#e6e0da)}
.card__photo--b{background:linear-gradient(120deg,#6f7780,#3b434c 50%,#8a9096)}
.card__photo--c{background:linear-gradient(120deg,#e9e4e0,#b52d2d 50%,#d7cfc8)}
.card__text{font-size:7px;line-height:1.45;color:var(--muted);padding:12px 9px 6px}
.more{font-size:6.5px;color:var(--blue);font-weight:600;padding:0 9px 10px;display:block}
.card__meta{border-top:1px solid var(--line);font-size:6px;color:var(--muted);padding:7px 9px;display:flex;gap:10px;align-items:center}
.card__meta svg{width:7px;height:7px;vertical-align:middle}

.quote__name{font-family:"Oswald",sans-serif;font-size:8px;font-weight:500;padding:8px 9px}
.quote__body{background:var(--blue);color:var(--white);padding:10px 9px 12px}
.quote__mark{font-size:20px;line-height:14px;font-family:"Oswald",sans-serif}
.quote__body p{font-size:9px;line-height:1.3;margin:6px 0 12px}
.quote__body .more{color:var(--white);padding:0}

/* form */
.quote-form{display:grid;grid-template-columns:repeat(3,166px);gap:10px 10px;justify-content:center}
.view--mobile .quote-form{grid-template-columns:220px}
.field{height:22px;border:1px solid var(--line);border-radius:3px;font-size:6.5px;color:#999999;text-align:left;padding:7px 8px}
.submit{display:inline-block;margin-top:14px;background:var(--blue);color:var(--white);font-size:7px;font-weight:600;padding:6px 16px;border-radius:2px}

/* certification */
.cert{padding:38px 0 32px 103px;text-align:left}
.view--mobile .cert{padding:36px 16px 30px;text-align:center}
.cert__top{display:flex;gap:40px;align-items:flex-start}
.view--mobile .cert__top{flex-direction:column;align-items:center;gap:16px}
.cert__copy{width:300px}
.view--mobile .cert__copy{width:auto}
.cert__title{font-size:16px;font-weight:600;margin-bottom:10px}
.view--mobile .cert__title{font-size:13px;border-bottom:2px solid var(--blue);display:inline-block}
.cert__copy p{font-size:7px;line-height:1.5;color:var(--muted)}
.badges{display:flex;gap:14px;margin-top:24px}
.view--mobile .badges{margin-top:0}
.badge{width:22px;height:36px;background:var(--red)}
.badge--wide{width:70px;height:36px;border:3px solid var(--red);background:var(--white)}
.badge--seal{width:48px;height:36px;background:var(--red);margin-left:14px}
.cert__lead{font-family:"Oswald",sans-serif;font-size:8px;font-weight:500;margin:18px 0 9px}
.chips{display:flex;flex-wrap:wrap;gap:8px 8px;width:640px;list-style:none}
.view--mobile .chips{width:auto;flex-direction:column;align-items:center;gap:10px}
.chips li{font-family:"Oswald",sans-serif;font-size:6.5px;font-weight:500;background:var(--white);border:1px solid var(--line);padding:5px 9px}
.chips li.is-active{background:var(--blue);color:var(--white);border-color:var(--blue)}

/* footer */
.footer{background:var(--dark);color:#bbbbbb;padding:22px 0 22px 103px;display:flex;gap:0;margin-top:26px}
.view--desktop .footer{height:150px}
.view--mobile .footer{flex-direction:column;padding:26px 14px;gap:22px;margin-top:0}
.footer__col{width:256px}
.footer__col--nav{width:173px}
.footer__head{font-size:6.5px;font-weight:600;color:var(--white);text-transform:uppercase;margin-bottom:10px;letter-spacing:.4px}
.tags{display:flex;flex-wrap:wrap;gap:4px;width:140px}
.tags span{font-size:6px;border:1px solid #555555;padding:2px 5px}
.tags span.is-active{background:var(--blue);border-color:var(--blue);color:var(--white)}
.links{list-style:none;font-size:6.5px;line-height:1.9;color:#6f9be8}
.links li::before{content:"› "}
.contact{font-size:6.5px;line-height:1.6}
.contact div{display:flex;gap:6px;margin-bottom:6px}
.contact svg{width:8px;height:8px;flex:none;margin-top:1px}
.bottom{background:var(--darker);color:#888888;font-size:6px;height:41px;display:flex;align-items:center;justify-content:space-between;padding:0 90px 0 103px}
.view--mobile .bottom{height:26px;padding:0 14px}
.bottom b{color:var(--white);font-weight:600}
</style>
</head>
<body>

<!-- Desktop layout -->
<main class="view view--desktop">
  <header class="hero">
    <div class="hero__photo" role="img" aria-label="Modern apartment buildings lit at dusk"></div>
    <div class="hero__shade"></div>
    <div class="hero__inner">
      <div class="brand"><span class="brand__mark"></span><span>R.T.Marlow<small>CONSTRUCTION LTD</small></span></div>
      <h1 class="hero__title">R.T.Marlow</h1>
      <ul class="services">
        <li class="is-active">Extensions</li><li>New build / New houses</li><li>Garden walls</li><li>Plastering</li><li>Brickwork</li><li>Groundworks</li>
      </ul>
    </div>
  </header>
  <nav class="menubar"><span>Contact Us</span><span>Case Studies</span><span>Testimonials</span><span>Certification</span><span>Membership</span>
    <svg class="menubar__search" width="8" height="8" viewBox="0 0 10 10"><circle cx="4" cy="4" r="3" fill="none" stroke="#aaa" stroke-width="1.2"/><line x1="6.2" y1="6.2" x2="9" y2="9" stroke="#aaa" stroke-width="1.2"/></svg></nav>

  <section class="section section--grey">
    <h2 class="section__title">Case Studies</h2>
    <div class="cards">
      <article class="card"><h3 class="card__title">Case Studies - 1</h3><div class="card__photo card__photo--a" role="img" aria-label="Model house and keys on a table"></div><p class="card__text">Consectetur adipiscing elit Sed do eiusmod tempor incididunt Ut labore et dolore magna aliqua.</p><span class="more">Learn More →</span><div class="card__meta"><span>◷ August 7, 2018</span><span>▭ 0</span></div></article>
      <article class="card"><h3 class="card__title">Case Studies - 2</h3><div class="card__photo card__photo--b" role="img" aria-label="Builder laying a brick wall"></div><p class="card__text">Consectetur adipiscing elit Sed do eiusmod tempor incididunt Ut labore et dolore magna aliqua.</p><span class="more">Learn More →</span><div class="card__meta"><span>◷ August 7, 2018</span><span>▭ 0</span></div></article>
      <article class="card"><h3 class="card__title">Case Studies - 3</h3><div class="card__photo card__photo--c" role="img" aria-label="Tools and plans on a work bench"></div><p class="card__text">Consectetur adipiscing elit Sed do eiusmod tempor incididunt Ut labore et dolore magna aliqua.</p><span class="more">Learn More →</span><div class="card__meta"><span>◷ August 7, 2018</span><span>▭ 0</span></div></article>
    </div>
    <h2 class="section__title" style="margin-top:44px">Testimonials</h2>
    <div class="cards">
      <article class="card"><h3 class="quote__name">Martin Ellwood</h3><div class="quote__body"><div class="quote__mark">“</div><p>“Consectetur adipiscing elit Sed do eiusmod tempor incididunt Ut labore et dolore magna aliqua.”</p><span class="more">Learn More →</span></div><div class="card__meta"><span>◷ August 7, 2018</span></div></article>
      <article class="card"><h3 class="quote__name">Martin Ellwood</h3><div class="quote__body"><div class="quote__mark">“</div><p>“Consectetur adipiscing elit Sed do eiusmod tempor incididunt Ut labore et dolore magna aliqua.”</p><span class="more">Learn More →</span></div><div class="card__meta"><span>◷ August 7, 2018</span></div></article>
      <article class="card"><h3 class="quote__name">Martin Ellwood</h3><div class="quote__body"><div class="quote__mark">“</div><p>“Consectetur adipiscing elit Sed do eiusmod tempor incididunt Ut labore et dolore magna aliqua.”</p><span class="more">Learn More →</span></div><div class="card__meta"><span>◷ August 7, 2018</span></div></article>
    </div>
  </section>

  <section class="section section--white">
    <h2 class="section__title">Contact Us For A Free Quote</h2>
    <div class="quote-form">
      <div class="field">First name*</div><div class="field">Last name*</div><div class="field">Email address*</div>
      <div class="field">Contact phone number*</div><div class="field">Post code*</div><div class="field">Description of the job required*</div>
    </div>
    <span class="submit">Submit →</span>
  </section>

  <section class="cert section--grey">
    <div class="cert__top">
      <div class="cert__copy"><h2 class="cert__title">Certification &amp; Prof. Membership</h2>
        <p>R.T.Marlow Construction is a registered company with the Guild of Quality Tradesmen (GQT). The GQT has a strict membership criteria &amp; dispute resolution service which gives our clients the confidence to entrust their residential building requirements with R.T.Marlow Construction.</p></div>
      <div class="badges"><span class="badge"></span><span class="badge--wide"></span><span class="badge--seal"></span></div>
    </div>
    <p class="cert__lead">GQT Membership means that R.T.Marlow Construction Ltd:</p>
    <ul class="chips">
      <li class="is-active">Has a minimum of twelve month trading</li><li>Been provided a professional reference</li><li>Confirmation of business address</li>
      <li>Has Public &amp; Employee Liability Insurance</li><li>Has signed up to the GQT Code of Practice</li><li>Been passed credit checks, public record &amp; director checks</li>
    </ul>
  </section>

  <footer class="footer">
    <div class="footer__col"><h4 class="footer__head">Our Services</h4><div class="tags"><span class="is-active">Extensions</span><span>New build</span><span>New houses</span><span>Garden walls</span><span>Plastering</span><span>Brickwork</span></div></div>
    <div class="footer__col footer__col--nav"><h4 class="footer__head">Navigation</h4><ul class="links"><li>Contact Us</li><li>Case Studies</li><li>Testimonials</li><li>Certification</li><li>Membership</li></ul></div>
    <div class="footer__col"><h4 class="footer__head">Contact Us</h4><div class="contact">
      <div><svg viewBox="0 0 10 10"><path d="M2 1l2 2-1 1.5c.8 1.5 1.7 2.4 3 3L7.5 6l2 2-1.5 1.5C4.5 9 1 5.5.5 2z" fill="#999"/></svg>01234 567890</div>
      <div><svg viewBox="0 0 10 10"><path d="M5 0a3.5 3.5 0 0 0-3.5 3.5C1.5 6 5 10 5 10s3.5-4 3.5-6.5A3.5 3.5 0 0 0 5 0zm0 5a1.5 1.5 0 1 1 0-3 1.5 1.5 0 0 1 0 3z" fill="#999"/></svg>Unit 4 Mill Lane Yard, Ashcombe, Westshire</div>
      <div><svg viewBox="0 0 10 10"><rect x="0.5" y="2" width="9" height="6" fill="none" stroke="#999"/><path d="M.5 2l4.5 3.5L9.5 2" fill="none" stroke="#999"/></svg>hello@rtmarlow.example</div></div></div>
  </footer>
  <div class="bottom"><span>© Copyright 2018 <b>R.T.Marlow Construction</b>. All Rights Reserved.</span><b>top ↑</b></div>
</main>

<!-- Mobile layout -->
<main class="view view--mobile">
  <header class="hero">
    <div class="hero__photo" role="img" aria-label="Modern apartment buildings lit at dusk"></div>
    <div class="hero__shade"></div>
    <div class="hero__inner">
      <div class="brand"><span class="brand__mark"></span><span>R.T.Marlow<small>CONSTRUCTION LTD</small></span></div>
      <h1 class="hero__title">R.T.Marlow</h1>
      <ul class="services">
        <li class="is-active">Extensions</li><li>New build / New houses</li><li>Garden walls</li><li>Plastering</li><li>Brickwork</li><li>Groundworks</li>
      </ul>
    </div>
  </header>
  <nav class="menubar"><svg width="10" height="8" viewBox="0 0 10 8"><path d="M0 1h10M0 4h10M0 7h10" stroke="#ccc" stroke-width="1.2"/></svg>
    <svg class="menubar__search" width="8" height="8" viewBox="0 0 10 10"><circle cx="4" cy="4" r="3" fill="none" stroke="#aaa" stroke-width="1.2"/><line x1="6.2" y1="6.2" x2="9" y2="9" stroke="#aaa" stroke-width="1.2"/></svg></nav>

  <section class="section section--white">
    <h2 class="section__title">Case Studies</h2>
    <div class="cards">
      <article class="card"><h3 class="card__title">Case Studies - 1</h3><div class="card__photo card__photo--a" role="img" aria-label="Model house and keys on a table"></div><p class="card__text">Consectetur adipiscing elit Sed do eiusmod tempor incididunt Ut labore et dolore magna aliqua.</p><span class="more">Learn More →</span><div class="card__meta"><span>◷ August 7, 2018</span><span>▭ 0</span></div></article>
      <article class="card"><h3 class="card__title">Case Studies - 2</h3><div class="card__photo card__photo--b" role="img" aria-label="Builder laying a brick wall"></div><p class="card__text">Consectetur adipiscing elit Sed do eiusmod tempor incididunt Ut labore et dolore magna aliqua.</p><span class="more">Learn More →</span><div class="card__meta"><span>◷ August 7, 2018</span><span>▭ 0</span></div></article>
      <article class="card"><h3 class="card__title">Case Studies - 3</h3><div class="card__photo card__photo--c" role="img" aria-label="Tools and plans on a work bench"></div><p class="card__text">Consectetur adipiscing elit Sed do eiusmod tempor incididunt Ut labore et dolore magna aliqua.</p><span class="more">Learn More →</span><div class="card__meta"><span>◷ August 7, 2018</span><span>▭ 0</span></div></article>
    </div>
    <h2 class="section__title" style="margin-top:40px">Testimonials</h2>
    <div class="cards">
      <article class="card"><h3 class="quote__name">Martin Ellwood</h3><div class="quote__body"><div class="quote__mark">“</div><p>“Consectetur adipiscing elit Sed do eiusmod tempor incididunt Ut labore et dolore magna aliqua.”</p><span class="more">Learn More →</span></div><div class="card__meta"><span>◷ August 7, 2018</span></div></article>
      <article class="card"><h3 class="quote__name">Martin Ellwood</h3><div class="quote__body"><div class="quote__mark">“</div><p>“Consectetur adipiscing elit Sed do eiusmod tempor incididunt Ut labore et dolore magna aliqua.”</p><span class="more">Learn More →</span></div><div class="card__meta"><span>◷ August 7, 2018</span></div></article>
      <article class="card"><h3 class="quote__name">Martin Ellwood</h3><div class="quote__body"><div class="quote__mark">“</div><p>“Consectetur adipiscing elit Sed do eiusmod tempor incididunt Ut labore et dolore magna aliqua.”</p><span class="more">Learn More →</span></div><div class="card__meta"><span>◷ August 7, 2018</span></div></article>
    </div>
  </section>

  <section class="section section--white" style="border-top:1px solid #e4e4e4">
    <h2 class="section__title">Contact Us For A Free Quote</h2>
    <div class="quote-form">
      <div class="field">First name*</div><div class="field">Last name*</div><div class="field">Contact phone number*</div>
      <div class="field">Email address*</div><div class="field">Post code*</div><div class="field">Description of the job required*</div>
    </div>
    <span class="submit">Submit →</span>
  </section>

  <section class="cert section--white" style="border-top:1px solid #e4e4e4">
    <div class="cert__top">
      <div class="cert__copy"><h2 class="cert__title">Certification &amp; Membership</h2>
        <p>R.T.Marlow Construction is a registered company with the Guild of Quality Tradesmen (GQT). The GQT has a strict membership criteria &amp; dispute resolution service which gives our clients the confidence to entrust their residential building requirements with R.T.Marlow Construction.</p></div>
      <div class="badges"><span class="badge"></span><span class="badge--wide"></span><span class="badge--seal"></span></div>
    </div>
    <p class="cert__lead">GQT Membership means that R.T.Marlow Construction Ltd</p>
    <ul class="chips">
      <li class="is-active">Has a minimum of twelve month trading</li><li>Been provided a professional reference</li><li>Confirmation of business address</li>
      <li>Has Public &amp; Employee Liability Insurance</li><li>Has signed up to the GQT Code of Practice</li><li>Been passed credit checks, public record &amp; director checks</li>
    </ul>
  </section>

  <footer class="footer">
    <div class="footer__col"><h4 class="footer__head">Our Services</h4><div class="tags"><span class="is-active">Extensions</span><span>New build</span><span>New houses</span><span>Garden walls</span><span>Plastering</span><span>Brickwork</span></div></div>
    <div class="footer__col"><h4 class="footer__head">Navigation</h4><ul class="links"><li>Contact Us</li><li>Case Studies</li><li>Testimonials</li><li>Certification</li><li>Membership</li></ul></div>
    <div class="footer__col"><h4 class="footer__head">Contact Us</h4><div class="contact">
      <div><svg viewBox="0 0 10 10"><path d="M2 1l2 2-1 1.5c.8 1.5 1.7 2.4 3 3L7.5 6l2 2-1.5 1.5C4.5 9 1 5.5.5 2z" fill="#999"/></svg>01234 567890</div>
      <div><svg viewBox="0 0 10 10"><path d="M5 0a3.5 3.5 0 0 0-3.5 3.5C1.5 6 5 10 5 10s3.5-4 3.5-6.5A3.5 3.5 0 0 0 5 0zm0 5a1.5 1.5 0 1 1 0-3 1.5 1.5 0 0 1 0 3z" fill="#999"/></svg>Unit 4 Mill Lane Yard, Ashcombe, Westshire</div>
      <div><svg viewBox="0 0 10 10"><rect x="0.5" y="2" width="9" height="6" fill="none" stroke="#999"/><path d="M.5 2l4.5 3.5L9.5 2" fill="none" stroke="#999"/></svg>hello@rtmarlow.example</div></div></div>
  </footer>
  <div class="bottom"><span>© Copyright 2018 <b>R.T.Marlow Construction</b>. All Rights Reserved.</span><b>top ↑</b></div>
</main>

</body>
</html>
```